Bring me business with this creative business card

Design my new business card. I am looking for something different with an impact. People will take a look at this card & they will 1- see how different & creative I am, 2-understand what I do 3- Call me to meet me!

I make videos with a message, testimonials. I am dynamic, fun, creative & human. My new website is in construction but in the meantime you can check this old one: brightpath.ca & another one Tidebloom.com & tidebloom facebook page.
I make videos. sometimes with a cameraman, sometimes with my phone. As an ex Public Relations agent, the message is the most important thing for me. I want to make my clients shine! When they start with me they often remind me of a lamb, when I finish coaching them they are powerful like LIONS! That's why I need a powerful business card!

Target Market(s)

Entrepreneurs, solo entrepreneurs, small & medium companies & start ups. People i will meet while networking. People that need videos on their website & social Networks to get attention, to be visible. men & women. From 35 to 49 years old.
I am an ex Public relations agent. I used to send clients in traditional medias, now with videos they have more chances to be seen on google the new media. I do videos of the president, his team, his loyal clients saying how great the company is & expert videos like series so people can be seen for example every 1 st of every month with a short 2 minute video. Also with my 20 years in marketing & communications I can coach & give tips to anybody who needs it.
Target: anybody who would like my old website brightpath.ca & I also have another website but it will be off line soon: tidebloom.com could give you ideas.

Industry/Entity Type

Communications

Contact Information for Business Card

I am in Montreal,So the business cards have to be the usual size like we have in Montreal: 9 cm x 5 cm
Details:My text: Mathilde Tessier Communication coach/Chief Lion. "Creating Videos as unique as you" off: 514-555-0147 cell: 514-555-0183. tidebloom.com
mathilde@tidebloom.com logo facebook, youtube, instagram

Colors
f37122

Requirements
Must have
• Dynamic, happy. Orange. Be creative in the look but NOT the shape of the card. Easy to read. Big enough to read.
Should not have
• No funny shapes: no round, no square, just the usual. I love creative but NOT on shape.

```html
<!DOCTYPE html>
<html lang="en">
<head>
<meta charset="utf-8">
<title>Tidebloom business card</title>
<link rel="stylesheet" href="https://fonts.googleapis.com/css2?family=Roboto+Condensed:wght@400;500;700&family=Roboto:wght@400&display=swap">
<style>
  :root {
    --orange: #f37122;
    --orange-deep: #ee5f22;
    --amber: #f7a21b;
    --ink: #1b1d1f;
    --paper: #f4f4f3;
    --text: #444446;
    --rule: #c9c9c9;
    --stage: #e9e4dc;
    --white: #ffffff;
  }
  * { margin: 0; padding: 0; box-sizing: border-box; }
  html, body { width: 1200px; height: 960px; overflow: hidden; }
  body { background: var(--stage); position: relative; font-family: "Roboto", sans-serif; }

  .card { position: absolute; width: 600px; height: 345px; overflow: hidden; }

  /* Front */
  .card-front { left: 325px; top: 105px; background: var(--ink); }
  .front-brand {
    position: absolute; left: 0; right: 0; top: 128px; text-align: center;
    font-family: "Roboto Condensed", sans-serif; font-weight: 700; font-size: 36px;
    letter-spacing: 1px; color: var(--orange); line-height: 1;
  }
  .front-slogan {
    position: absolute; left: 0; right: 0; top: 184px; text-align: center;
    font-family: "Roboto Condensed", sans-serif; font-weight: 500; font-size: 15px;
    color: var(--orange); line-height: 1;
  }
  .social-row { position: absolute; left: 178px; top: 207px; }

  /* Back */
  .card-back { left: 320px; top: 493px; background: var(--paper); }
  .brand-mark {
    position: absolute; left: 139px; top: 94px; width: 76px; height: 76px;
    border-radius: 50%; background: var(--orange);
  }
  .brand-name {
    position: absolute; left: 57px; width: 240px; top: 196px; text-align: center;
    font-family: "Roboto Condensed", sans-serif; font-weight: 700; font-size: 30px;
    letter-spacing: 1px; color: var(--orange); line-height: 1;
  }
  .divider { position: absolute; left: 288px; top: 92px; width: 1px; height: 150px; background: var(--rule); }

  .person { position: absolute; left: 315px; top: 95px; }
  .person-name {
    font-family: "Roboto Condensed", sans-serif; font-weight: 700; font-size: 23px;
    color: var(--orange-deep); text-transform: uppercase; line-height: 1.1;
  }
  .person-role {
    margin-top: 3px; font-family: "Roboto Condensed", sans-serif; font-weight: 500; font-size: 16px;
    color: var(--amber); text-transform: uppercase; line-height: 1.2;
  }
  .contact-list { list-style: none; margin-top: 11px; }
  .contact-list li {
    display: flex; align-items: center; gap: 9px; height: 19px;
    font-size: 14px; color: var(--text);
  }
  .contact-list svg { width: 13px; height: 13px; flex: none; }

  .band-amber { position: absolute; left: 0; top: 324px; width: 365px; height: 6px; background: var(--amber); }
  .band-orange { position: absolute; left: 0; top: 332px; width: 365px; height: 5px; background: var(--orange-deep); }
  .web-tab { position: absolute; left: 355px; top: 309px; width: 245px; height: 36px; }
  .web-address {
    position: absolute; left: 410px; top: 318px; font-size: 14px;
    letter-spacing: 1.5px; color: var(--white); line-height: 1;
  }
</style>
</head>
<body>

<section class="card card-front" aria-label="Card front">
  <div class="front-brand">TIDEBLOOM</div>
  <div class="front-slogan">Creating Videos as unique as you</div>
  <svg class="social-row" width="252" height="22" viewBox="0 0 252 22" aria-label="Social links">
    <line x1="0" y1="11" x2="84" y2="11" stroke="#ffffff" stroke-width="1"/>
    <circle cx="97" cy="11" r="10" fill="#f37122"/>
    <circle cx="121" cy="11" r="10" fill="#f37122"/>
    <circle cx="145" cy="11" r="10" fill="#f37122"/>
    <line x1="160" y1="11" x2="252" y2="11" stroke="#ffffff" stroke-width="1"/>
  </svg>
</section>

<section class="card card-back" aria-label="Card back">
  <div class="brand-mark"></div>
  <div class="brand-name">TIDEBLOOM</div>
  <div class="divider"></div>

  <div class="person">
    <div class="person-name">Mathilde T.</div>
    <div class="person-role">Communication Coach<br>Chief Lion</div>
    <ul class="contact-list">
      <li>
        <svg viewBox="0 0 24 24"><path fill="#ee5f22" d="M6.6 10.8a15.1 15.1 0 0 0 6.6 6.6l2.2-2.2c.3-.3.7-.4 1-.2 1.1.4 2.3.6 3.6.6.6 0 1 .4 1 1V20c0 .6-.4 1-1 1A17 17 0 0 1 3 4c0-.6.4-1 1-1h3.5c.6 0 1 .4 1 1 0 1.3.2 2.5.6 3.6.1.3 0 .7-.2 1z"/></svg>
        514-555-0147
      </li>
      <li>
        <svg viewBox="0 0 24 24"><rect x="6" y="1.5" width="12" height="21" rx="2" fill="none" stroke="#ee5f22" stroke-width="2.4"/><circle cx="12" cy="18.5" r="1.3" fill="#ee5f22"/></svg>
        514-555-0183.
      </li>
      <li>
        <svg viewBox="0 0 24 24"><rect x="2" y="5" width="20" height="14" fill="#ee5f22"/><path d="M2 5l10 8 10-8" fill="none" stroke="#f4f4f3" stroke-width="1.6"/></svg>
        mathilde@tidebloom.com
      </li>
    </ul>
  </div>

  <div class="band-amber"></div>
  <div class="band-orange"></div>
  <svg class="web-tab" viewBox="0 0 245 36" aria-hidden="true">
    <path d="M0 36 C12 36 14 26 18 12 C21 3 25 0 34 0 H245 V36 Z" fill="#ffffff"/>
    <path d="M5 36 C16 36 18 27 22 14 C25 5 29 2 37 2 H245 V36 Z" fill="#ee5f22"/>
  </svg>
  <div class="web-address">www.tidebloom.com</div>
</section>

</body>
</html>
```